Business card design for holistic health care clinic

We need a double-sided business card design for our holistic health care clinic that integrates our logo design and also its color scheme. My business is called Valmira. It is an integrative medicine clinic. You have already done the logo for me. Please ensure an elegant and upscale design that is not cluttered, but still has all the necessary information (please see below for details).

Target Market(s)

Wellness, fitness, rehabilitation for educated, well-traveled open-minded clients who are focused on natural, organic, balanced and preventive healthcare and lifestyle.

Industry/Entity Type

Medical

Contact Information for Business Card

Modern, clean.

Number of Pages Required

1 page

Font styles to use
Serif
Sans Serif

Colors

Designer to choose colors to be used in the design.

Requirements
Must have
• Logo on one side, all other information on the other side.
• Other information should include:
• Tobias Wrenfeld - DOE, CPT, LMT
• 4100 East Marrow Drive
• Austin, TX 78119
• 512 555 0148
• 818 555 0192
• info@ValmiraHealth.example
• t.wrenfeld@ValmiraHealth.example
Nice to have
• Darker background on front - but not totally black - shaded/dark gray.

```html
<!DOCTYPE html>
<html lang="en">
<head>
<meta charset="utf-8">
<title>Valmira Business Card</title>
<link href="https://fonts.googleapis.com/css2?family=Montserrat:wght@400;500;700&family=Oswald:wght@500&display=swap" rel="stylesheet">
<style>
  :root {
    --stage: #2b2b2d;
    --brand-blue: #1a93d0;
    --card-white: #ffffff;
    --band-dark: #2a2a2a;
    --text-light: #e6e6e6;
    --text-muted: #bdbdbd;
    --text-grey: #555555;
  }
  * { margin: 0; padding: 0; box-sizing: border-box; }
  html, body { width: 1200px; height: 852px; overflow: hidden; }
  body {
    background: var(--stage);
    font-family: "Montserrat", sans-serif;
    display: flex;
    align-items: center;
    justify-content: center;
    gap: 30px;
  }
  .card {
    width: 555px;
    height: 317px;
    border-radius: 18px;
    position: relative;
    overflow: hidden;
  }
  .card-front {
    background: var(--brand-blue);
    display: flex;
    align-items: center;
    justify-content: center;
  }
  .brand {
    display: flex;
    align-items: center;
    gap: 14px;
    font-family: "Montserrat", sans-serif;
    font-weight: 700;
    letter-spacing: 2px;
  }
  .brand-dot { border-radius: 50%; flex: none; }
  .card-front .brand { color: var(--card-white); font-size: 56px; }
  .card-front .brand-dot { width: 26px; height: 26px; background: var(--card-white); }

  .card-back { background: var(--card-white); }
  .card-back .brand {
    position: absolute;
    top: 58px;
    left: 0; right: 0;
    justify-content: center;
    color: var(--brand-blue);
    font-size: 48px;
  }
  .card-back .brand-dot { width: 22px; height: 22px; background: var(--brand-blue); }

  .contact-band {
    position: absolute;
    left: 0; right: 0;
    top: 176px;
    height: 100px;
    background: var(--band-dark);
    display: flex;
    align-items: center;
    padding: 0 36px;
  }
  .person { width: 190px; }
  .person-name {
    font-family: "Oswald", sans-serif;
    font-weight: 500;
    color: var(--brand-blue);
    font-size: 26px;
    line-height: 1.1;
    text-transform: uppercase;
  }
  .person-title {
    font-size: 12px;
    color: var(--text-muted);
    margin-top: 4px;
    letter-spacing: 0.5px;
  }
  .divider {
    width: 1.5px;
    height: 62px;
    background: var(--text-muted);
    margin: 0 22px 0 6px;
  }
  .contact-list { list-style: none; }
  .contact-list li {
    display: flex;
    align-items: center;
    gap: 9px;
    font-size: 11.5px;
    color: var(--text-light);
    line-height: 19px;
  }
  .contact-list svg { width: 11px; height: 11px; flex: none; }
  .address {
    position: absolute;
    left: 0; right: 0;
    top: 288px;
    text-align: center;
    font-size: 11.5px;
    color: var(--text-grey);
    letter-spacing: 0.4px;
  }
</style>
</head>
<body>
  <section class="card card-front" aria-label="Card front">
    <div class="brand"><span class="brand-dot"></span>VALMIRA</div>
  </section>

  <section class="card card-back" aria-label="Card back">
    <div class="brand"><span class="brand-dot"></span>VALMIRA</div>

    <div class="contact-band">
      <div class="person">
        <p class="person-name">Tobias Wrenfeld</p>
        <p class="person-title">DOE, CPT, LMT</p>
      </div>
      <div class="divider"></div>
      <ul class="contact-list">
        <li>
          <svg viewBox="0 0 24 24" fill="var(--brand-blue)"><path d="M6.6 10.8a15.1 15.1 0 0 0 6.6 6.6l2.2-2.2a1 1 0 0 1 1-.25 11.4 11.4 0 0 0 3.6.57 1 1 0 0 1 1 1V20a1 1 0 0 1-1 1A17 17 0 0 1 3 4a1 1 0 0 1 1-1h3.5a1 1 0 0 1 1 1c0 1.25.2 2.45.57 3.57a1 1 0 0 1-.25 1z"/></svg>
          512 555 0148
        </li>
        <li>
          <svg viewBox="0 0 24 24" fill="none" stroke="var(--brand-blue)" stroke-width="2.5"><rect x="6" y="2" width="12" height="20" rx="2"/><line x1="11" y1="18" x2="13" y2="18"/></svg>
          818 555 0192
        </li>
        <li>
          <svg viewBox="0 0 24 24" fill="none" stroke="var(--brand-blue)" stroke-width="2.5"><rect x="2" y="5" width="20" height="14" rx="1"/><polyline points="2,6 12,13 22,6"/></svg>
          info@ValmiraHealth.example
        </li>
        <li>
          <svg viewBox="0 0 24 24" fill="none" stroke="var(--brand-blue)" stroke-width="2.2"><circle cx="12" cy="12" r="10"/><ellipse cx="12" cy="12" rx="4.5" ry="10"/><line x1="2" y1="12" x2="22" y2="12"/></svg>
          t.wrenfeld@ValmiraHealth.example
        </li>
      </ul>
    </div>

    <p class="address">4100 East Marrow Drive Austin, TX 78119</p>
  </section>
</body>
</html>
```